Clean business card with logo provided

I want a card that will stand out among the masses. I need the color and image to show professionalism and yet have a family appeal showing that I only deal with win/win scenarios. The back of the card will be used to take notes about the individual so I can use that in my database entry. I like modern design but need professionalism in it also. It needs to fit my "clean, safe, and affordable housing" motto. I need to be able to write on the file and update the card details for my employees.

Target Market(s)

Investors looking to make investment income through real estate

Industry/Entity Type

Real Estate

Contact Information for Business Card

Brent Kovalich
blank address, city, st, zip code
480-555-3174
brentkovalich@ridgeworthrentals.example
www.ridgeworthrentals.example

Font styles to use
Sans Serif

Requirements
Must have
• I would like the back of the card to have lines for info. example
• Met/Visited: Date:
• Interets:
Nice to have
• I want the cards color to match the logo background color. Font with details to be san serif and black. I want the card rectangular with square corners. Standard business card size. I would like to see cards designed with both images to see which i prefer more.

```html
<!DOCTYPE html>
<html lang="en">
<head>
<meta charset="UTF-8">
<title>Ridgeworth Rentals LLC – Business Card</title>
<link href="https://fonts.googleapis.com/css2?family=Source+Sans+3:wght@400;600;700&display=swap" rel="stylesheet">
<style>
  :root {
    --stage: #151515;
    --card-front: #f4f4f4;
    --card-back: #ececec;
    --teal: #1aaac8;
    --ink: #111111;
    --dots: #222222;
  }
  * { margin: 0; padding: 0; box-sizing: border-box; }
  html, body {
    width: 1200px; height: 900px; overflow: hidden;
    background: var(--stage);
    font-family: "Source Sans 3", "Myriad Pro", sans-serif;
  }
  .stage { position: relative; width: 1200px; height: 900px; }
  .card {
    position: absolute; top: 184px;
    width: 302px; height: 491px;
    border-radius: 11px;
    text-align: center;
    overflow: hidden;
  }
  .card--front { left: 299px; background: var(--card-front); }
  .card--back { left: 645px; width: 305px; background: var(--card-back); }

  .brand { position: absolute; left: 0; right: 0; top: 58px; }
  .brand__name {
    display: flex; align-items: center; justify-content: center; gap: 7px;
    height: 24px; white-space: nowrap;
    color: var(--teal); font-weight: 600;
    font-size: 16px; letter-spacing: 1.2px; text-transform: uppercase;
  }
  .brand__dot { width: 10px; height: 10px; border-radius: 50%; background: var(--teal); flex: none; }
  .brand__tagline {
    margin-top: 35px; color: var(--teal);
    font-size: 8.5px; font-weight: 600;
  }

  .holder {
    position: absolute; left: 0; right: 0; top: 266px;
    color: var(--teal); font-size: 18px; font-weight: 700; letter-spacing: .3px;
    text-transform: uppercase;
  }
  .address {
    position: absolute; left: 0; right: 0; top: 332px;
    color: var(--ink); font-size: 13.5px; line-height: 15px;
  }
  .contacts { position: absolute; left: 0; right: 0; top: 397px; list-style: none; }
  .contacts li {
    display: flex; align-items: center; justify-content: center; gap: 5px;
    height: 21px; color: var(--ink); font-size: 13.5px; white-space: nowrap;
  }
  .contacts svg { width: 10px; height: 10px; fill: var(--teal); flex: none; }

  .notes { position: absolute; left: 0; right: 0; top: 266px; }
  .notes__label {
    height: 70px; position: relative;
    color: var(--teal); font-size: 15px; font-weight: 600; text-transform: uppercase;
  }
  .notes__line {
    position: absolute; left: 40px; right: 40px; top: 47px;
    border-bottom: 2px dotted var(--dots);
  }
  .notes__line--short { left: 48px; right: 48px; }
  .notes__line--wide { left: 36px; right: 36px; }
</style>
</head>
<body>
<main class="stage">
  <section class="card card--front" aria-label="Card front">
    <header class="brand">
      <div class="brand__name"><span class="brand__dot"></span>Ridgeworth Rentals LLC</div>
      <p class="brand__tagline">Providing clean, safe, and affordable housing</p>
    </header>
    <h1 class="holder">Brent Kovalich</h1>
    <p class="address">12345, Address Goes Here<br>Country Name, 123456</p>
    <ul class="contacts">
      <li><svg viewBox="0 0 24 24"><path d="M6.6 10.8a15.2 15.2 0 0 0 6.6 6.6l2.2-2.2a1 1 0 0 1 1-.25 11.4 11.4 0 0 0 3.6.57 1 1 0 0 1 1 1V20a1 1 0 0 1-1 1A17 17 0 0 1 3 4a1 1 0 0 1 1-1h3.5a1 1 0 0 1 1 1c0 1.25.2 2.45.57 3.57a1 1 0 0 1-.25 1z"/></svg>480-555-3174</li>
      <li><svg viewBox="0 0 24 24"><path d="M2 5h20v14H2z"/><path d="M2 5l10 8 10-8" fill="none" stroke="#f4f4f4" stroke-width="2"/></svg>brentkovalich@ridgeworthrentals.example</li>
      <li><svg viewBox="0 0 24 24"><circle cx="12" cy="12" r="11"/></svg>www.ridgeworthrentals.example</li>
    </ul>
  </section>

  <section class="card card--back" aria-label="Card back">
    <header class="brand">
      <div class="brand__name"><span class="brand__dot"></span>Ridgeworth Rentals LLC</div>
      <p class="brand__tagline">Providing clean, safe, and affordable housing</p>
    </header>
    <div class="notes">
      <div class="notes__label">Visited Date<span class="notes__line notes__line--short"></span></div>
      <div class="notes__label">Interets<span class="notes__line notes__line--wide"></span></div>
      <div class="notes__label">Problems<span class="notes__line"></span></div>
    </div>
  </section>
</main>
</body>
</html>
```